TA BRAMLEY BUSINESS CARD DESIGN PROJECT

We need to utilize our logo that was expertly created on PixelHarbor and now need to match this with a business card design.

```html
<!DOCTYPE html>
<html lang="en">
<head>
<meta charset="utf-8">
<title>TA Bramley Business Card</title>
<link rel="stylesheet" href="https://fonts.googleapis.com/css2?family=Montserrat:wght@400;700&display=swap">
<style>
  :root {
    --page-bg: #d8d3cd;
    --card-light: #eeebe7;
    --card-dark: #1c1c1e;
    --brand-blue: #1d4f8f;
    --text-light: #e4e0da;
    --icon-blue: #3d6599;
  }
  html, body {
    margin: 0;
    padding: 0;
    width: 1200px;
    height: 1047px;
    overflow: hidden;
    background: var(--page-bg);
  }
  .business-card {
    position: absolute;
    left: 100px;
    top: 252px;
    width: 1000px;
    height: 543px;
    filter: drop-shadow(0 10px 24px rgba(0,0,0,0.18));
  }
  .business-card svg { display: block; width: 100%; height: 100%; }
  .card-face { fill: var(--card-light); }
  .dark-panel { fill: var(--card-dark); }
  .swoosh { fill: var(--brand-blue); }
  .accent-bar { fill: var(--brand-blue); }
  .brand-name {
    font-family: "Montserrat", sans-serif;
    font-weight: 700;
    fill: var(--brand-blue);
    font-size: 50px;
    letter-spacing: 4px;
  }
  .person-name {
    font-family: "Montserrat", sans-serif;
    font-weight: 700;
    fill: var(--brand-blue);
    font-size: 27px;
  }
  .detail {
    font-family: "Montserrat", sans-serif;
    font-weight: 400;
    fill: var(--text-light);
    font-size: 20px;
  }
  .icon { fill: var(--icon-blue); }
  .icon-line { fill: none; stroke: var(--card-dark); stroke-width: 1.2; }
</style>
</head>
<body>
  <div class="business-card">
    <svg viewBox="0 0 880 478" xmlns="http://www.w3.org/2000/svg">
      <defs>
        <clipPath id="card-shape">
          <rect x="0" y="0" width="880" height="478" rx="18" ry="18"/>
        </clipPath>
      </defs>
      <g clip-path="url(#card-shape)">
        <rect class="card-face" x="0" y="0" width="880" height="478"/>
        <path class="dark-panel" d="M580,0 C625,45 612,115 560,175 C478,270 336,360 322,478 L880,478 L880,0 Z"/>
        <path class="swoosh" d="M584,22 C618,72 602,135 552,192 C472,285 342,360 318,430 C328,350 452,268 532,190 C588,132 602,72 584,22 Z"/>
      </g>

      <text class="brand-name" x="42" y="150">TA BRAMLEY</text>

      <rect class="accent-bar" x="854" y="188" width="24" height="60"/>
      <text class="person-name" x="838" y="210" text-anchor="end">ELLIS CARTER</text>
      <text class="detail" x="838" y="240" text-anchor="end">Managing Director</text>

      <text class="detail" x="812" y="297" text-anchor="end">123 456 789</text>
      <text class="detail" x="812" y="327" text-anchor="end">info@youremail.com</text>
      <text class="detail" x="812" y="357" text-anchor="end">www.yourwebsite.com</text>

      <!-- phone -->
      <path class="icon" d="M822,292 q9,-6 18,0 l-2,3 h-3 l-1,-2 h-6 l-1,2 h-3 Z M825,295 h12 v6 h-12 Z"/>
      <!-- envelope -->
      <rect class="icon" x="824" y="318" width="15" height="10" rx="1"/>
      <path class="icon-line" d="M824,319 L831.5,324 L839,319"/>
      <!-- globe -->
      <circle class="icon" cx="831.5" cy="352" r="7.5"/>
      <path class="icon-line" d="M824,352 H839 M831.5,344.5 V359.5"/>

      <text class="detail" x="843" y="407" text-anchor="end">Your address, City</text>
      <text class="detail" x="843" y="438" text-anchor="end">State, Zip 1234</text>
    </svg>
  </div>
</body>
</html>
```